Tolbek cards

I want a simple business card that pops.
Logo on one side.
On side two i want.
"Are you thinking about a new building on your property, or renovating an existing structure? Contact".....
Owners Name: Dale Whitacre
Owners Phone number: 610-555-0187
Address:4076 Copper Ridge RD, Halden, PA 15980
Committed to Quality, Service, and Integrity

```html
<!DOCTYPE html>
<html lang="en">
<head>
<meta charset="utf-8">
<title>Tolbek Builders LLC – Business Card</title>
<link rel="stylesheet" href="https://fonts.googleapis.com/css2?family=Archivo:wght@800&family=Roboto:wght@300;400;700&display=swap">
<style>
  :root {
    --bg: #232323;
    --card: #ececea;
    --brown-dark: #4a3426;
    --brown-deep: #4b3526;
    --tan: #a08467;
    --tan-dark: #6e5239;
    --text-dark: #3b2a1f;
    --text-light: #f3eee8;
    --rule: #b9aa98;
  }
  * { margin: 0; padding: 0; box-sizing: border-box; }
  html, body { width: 1200px; height: 576px; overflow: hidden; background: var(--bg); }
  .canvas { position: relative; width: 1200px; height: 576px; }

  .card {
    position: absolute; top: 138px; width: 484px; height: 293px;
    border-radius: 10px; overflow: hidden; background: var(--card);
  }
  .card--front { left: 102px; }
  .card--back { left: 596px; width: 480px; }

  /* Front */
  .front-brand {
    position: absolute; left: 0; right: 0; top: 140px; text-align: center;
    font-family: "Archivo", sans-serif; font-weight: 800; color: var(--brown-dark);
  }
  .front-brand__name { display: block; font-size: 52px; line-height: 1; letter-spacing: 1px; }
  .front-brand__suffix { display: block; font-size: 17px; letter-spacing: 2.5px; margin-top: 4px; }
  .tagline-band {
    position: absolute; left: 0; right: 0; bottom: 0; height: 30px;
    background: linear-gradient(90deg, var(--tan), var(--tan-dark));
    color: var(--text-light); font-family: "Roboto", sans-serif; font-size: 13px;
    display: flex; align-items: center; justify-content: center;
  }

  /* Back */
  .back-shapes { position: absolute; inset: 0; }
  .pitch {
    position: absolute; left: 42px; top: 46px; width: 122px;
    font-family: "Roboto", sans-serif; font-weight: 300; font-size: 18px; line-height: 25px;
    color: var(--text-light);
  }
  .contact-label {
    position: absolute; left: 248px; top: 47px; width: 205px;
    display: flex; align-items: center; gap: 6px;
    font-family: "Roboto", sans-serif; font-size: 8.5px; color: var(--text-dark);
  }
  .contact-label::after { content: ""; flex: 1; height: 1px; background: var(--rule); }
  .back-brand {
    position: absolute; left: 248px; top: 74px;
    font-family: "Archivo", sans-serif; font-weight: 800; color: var(--brown-dark);
  }
  .back-brand__name { display: block; font-size: 31px; line-height: 1; letter-spacing: 0.5px; }
  .back-brand__suffix { display: block; font-size: 9.5px; letter-spacing: 4.2px; margin-top: 2px; }
  .owner {
    position: absolute; left: 248px; top: 137px;
    font-family: "Roboto", sans-serif; font-weight: 700; font-size: 19px; color: var(--text-dark);
  }
  .owner__surname { color: var(--tan); }
  .contact-list {
    position: absolute; left: 248px; top: 167px; list-style: none;
    font-family: "Roboto", sans-serif; font-size: 13px; line-height: 16px; color: var(--text-dark);
  }
  .contact-list li { display: flex; gap: 7px; margin-bottom: 4px; }
  .contact-list svg { flex: none; margin-top: 2px; }
  .back-tagline {
    position: absolute; left: 248px; top: 252px;
    font-family: "Roboto", sans-serif; font-size: 11.5px; color: var(--text-light);
  }
</style>
</head>
<body>
<main class="canvas">

  <section class="card card--front" aria-label="Card front">
    <div class="front-brand">
      <span class="front-brand__name">TOLBEK</span>
      <span class="front-brand__suffix">BUILDERS LLC</span>
    </div>
    <div class="tagline-band">Committed to Quality, Service &amp; Integrity</div>
  </section>

  <section class="card card--back" aria-label="Card back">
    <svg class="back-shapes" width="480" height="293" viewBox="0 0 480 293" aria-hidden="true">
      <polygon points="205,246 480,246 480,274 195,274" fill="var(--tan)"/>
      <path d="M0,0 H170 Q270,150 180,293 H0 Z" fill="var(--tan)"/>
      <path d="M0,0 H164 Q258,150 166,293 H0 Z" fill="var(--brown-deep)"/>
    </svg>

    <p class="pitch">Are you thinking about a new building on your property, or renovating an existing structure?</p>

    <div class="contact-label">Contact:</div>
    <div class="back-brand">
      <span class="back-brand__name">TOLBEK</span>
      <span class="back-brand__suffix">BUILDERS LLC</span>
    </div>

    <p class="owner">DALE <span class="owner__surname">WHITACRE</span></p>

    <ul class="contact-list">
      <li>
        <svg width="12" height="12" viewBox="0 0 12 12" aria-hidden="true">
          <circle cx="6" cy="6" r="5.3" fill="none" stroke="var(--text-dark)" stroke-width="0.9"/>
          <path d="M4.1,3.2 L5,4.6 L4.5,5.2 Q5.2,6.6 6.6,7.3 L7.2,6.8 L8.6,7.7 L8,8.6 Q5.5,8.6 3.3,4 Z" fill="var(--text-dark)"/>
        </svg>
        <span>610-555-0187</span>
      </li>
      <li>
        <svg width="12" height="12" viewBox="0 0 12 12" aria-hidden="true">
          <circle cx="6" cy="6" r="5.3" fill="none" stroke="var(--text-dark)" stroke-width="0.9"/>
          <path d="M6,2.6 A2.2,2.2 0 0 1 8.2,4.8 Q8.2,6.4 6,9.2 Q3.8,6.4 3.8,4.8 A2.2,2.2 0 0 1 6,2.6 Z" fill="var(--text-dark)"/>
          <circle cx="6" cy="4.8" r="0.8" fill="var(--card)"/>
        </svg>
        <span>4076 Copper Ridge RD,<br>Halden, PA 15980</span>
      </li>
    </ul>

    <p class="back-tagline">Committed to Quality, Service &amp; Integrity</p>
  </section>

</main>
</body>
</html>
```